****Business Card Design for Quarrystone Development. Design based around attached logo/company name

I’m looking for business card design for my company Quarrystone Development Group,LLC. Design should be professional, sharp and minimal. Outside of the attached logos, greyscale colors for remainder of cards. My thoughts are two-sided card with attached logo on one side and my info on the other but open to one-sided as well with right design.
Target Market(s)
Real estate professionals including banks, private investors, property owners, developers, commercial tenants like Brewlantern, Grovika or Tanquist’s.
Industry/Entity Type
Commercial real estate development and investments.
Contact Information for Business Card
Name, title, email, phone #’s, web address and physical address
Font styles to use
Other font styles liked:
- Helvetica, Garamond, etc
Colors
Designer to choose only greyscale colors for use in the design.
Requirements
Must have
- Attached logo first or second options.
Nice to have
- Two sided card with logo on one side. Attached Logo/company name can be laid out any way that flows as long as it’s legible.name
Should not have
- No loud colors. ***Please do not include logo, I have removed the company design with a logo image.

```html
<!DOCTYPE html>
<html lang="en">
<head>
<meta charset="utf-8">
<title>Quarrystone Development Group, LLC — Business Card</title>
<link href="https://fonts.googleapis.com/css2?family=Arimo:wght@400&family=EB+Garamond:wght@400&family=Libre+Baskerville:wght@700&display=swap" rel="stylesheet">
<style>
  :root {
    --page-bg: #dcdcdc;
    --card-bg: #ffffff;
    --ink-slate: #4b5469;
    --ink-grey: #7b7b7b;
    --band-dark: #5c6577;
    --band-light: #8f8f8f;
  }
  * { margin: 0; padding: 0; box-sizing: border-box; }
  html, body {
    width: 1200px;
    height: 1059px;
    overflow: hidden;
    background: var(--page-bg);
  }
  .card {
    position: absolute;
    left: 222px;
    top: 310px;
    width: 816px;
    height: 431px;
    background: var(--card-bg);
    border-radius: 18px;
    overflow: hidden;
  }
  .company-name {
    position: absolute;
    left: 38px;
    top: 56px;
    font-family: "EB Garamond", Garamond, serif;
    font-weight: 400;
    color: var(--ink-slate);
    line-height: 1;
  }
  .company-name .primary {
    display: block;
    font-size: 40px;
    letter-spacing: 1.5px;
  }
  .company-name .secondary {
    display: block;
    margin-top: 6px;
    font-size: 18px;
    letter-spacing: 1.6px;
  }
  .contact {
    position: absolute;
    left: 38px;
    top: 198px;
    font-family: "Arimo", Helvetica, Arial, sans-serif;
    font-size: 16.5px;
    color: var(--ink-grey);
  }
  .address { line-height: 24px; }
  .contact-list { list-style: none; margin-top: 14px; }
  .contact-list li {
    display: flex;
    align-items: center;
    height: 29px;
  }
  .contact-list svg {
    width: 13px;
    height: 13px;
    margin-right: 8px;
    fill: var(--ink-slate);
  }
  .person {
    position: absolute;
    right: 95px;
    top: 192px;
    text-align: right;
  }
  .person-name {
    font-family: "Libre Baskerville", Georgia, serif;
    font-weight: 700;
    font-size: 22px;
    letter-spacing: 0.3px;
    color: var(--ink-slate);
  }
  .person-title {
    margin-top: 6px;
    font-family: "Arimo", Helvetica, Arial, sans-serif;
    font-size: 16.5px;
    color: var(--ink-grey);
  }
  .wave {
    position: absolute;
    left: 0;
    top: 0;
    width: 816px;
    height: 431px;
  }
</style>
</head>
<body>
  <div class="card">
    <svg class="wave" viewBox="0 0 816 431" aria-hidden="true">
      <path d="M0,355 C60,392 150,398 240,396 C400,390 560,340 680,340 C750,341 800,364 816,376 V431 H0 Z" fill="var(--band-light)"/>
      <path d="M0,359 C60,396 150,401 240,399 C400,393 560,352 680,354 C750,356 800,378 816,388 V431 H0 Z" fill="#ffffff"/>
      <path d="M0,363 C60,400 150,405 240,402 C400,396 560,358 680,362 C750,364 800,380 816,392 V431 H0 Z" fill="var(--band-dark)"/>
    </svg>

    <div class="company-name">
      <span class="primary">QUARRYSTONE</span>
      <span class="secondary">DEVELOPMENT GROUP, LLC</span>
    </div>

    <div class="contact">
      <p class="address">8474 Street Address Name<br>Counter name AB 7841</p>
      <ul class="contact-list">
        <li>
          <svg viewBox="0 0 16 16"><path d="M3.5 1.5l2.3 0.3 1 3.2-1.6 1.3c0.9 1.9 2.4 3.4 4.3 4.3l1.3-1.6 3.2 1 0.3 2.3c0 0.7-0.6 1.3-1.3 1.2C7.4 13.2 2.8 8.6 2.3 2.8 2.2 2.1 2.8 1.5 3.5 1.5z"/></svg>
          (123)-555-0194
        </li>
        <li>
          <svg viewBox="0 0 16 16"><path d="M1 3.5h14v1.2L8 9 1 4.7z M1 6.3l7 4.3 7-4.3V12.5H1z"/></svg>
          info@quarrystonedevelopment.com
        </li>
        <li>
          <svg viewBox="0 0 16 16"><circle cx="8" cy="8" r="7"/><path d="M8 1.5v13M1.5 8h13M3 4.5h10M3 11.5h10" stroke="#fff" stroke-width="1" fill="none"/></svg>
          www.quarrystonedevelopment.com
        </li>
      </ul>
    </div>

    <div class="person">
      <p class="person-name">ELIAS WARRICK</p>
      <p class="person-title">Founder/CEO</p>
    </div>
  </div>
</body>
</html>
```